UI/UX Re-Do for TallyNest - a free to use project management platform for desktop and mobile.

UI/UX Re-Do for TallyNest
TallyNest is a free to use project management platform for desktop and mobile.
We are looking for help with our UI/UX re-design.
As of now the platform is totally functional.
The problem is around flow and look. We want TN to become something that any one can use to manage and even socialize any project. A project can be something work related like organizing a team around a software build, marketing campaign, shared client file space, etc... In fact, most of our current members are using TN for just such work projects.
We also see a project as planning a wedding, organizing a group trip, a simple to-do list, organizing a kids sports team, and so on...
To become a platform that people will use in their work and personal life we first need to become more intuitive and friendly - while maintaining advanced functionality for more advanced needs.
We need help to beautify, streamline, and simplify - while keeping all the functions.
The quickest way to understand TN, and our current issues is this short video:
https://vidlumo.example/w/Qa7KdP2mXzR
For sure see this link for the entire most recent description AND images:
https://tallynestapp.example/?p=HumbZ4KcWrT
The best way to understand TN is to actually use it:
https://tallynestapp.example
Should you choose to take a run at improving TN here are the details:
Please focus your ideas for mobile, it's where we have the biggest issues.
Feel free to get outside the box.
Avoid swipe oriented designs.
Feel free to focus on ideas over polished outputs.
Use any tool you like, PS, hand drawing, written description if you think that works best.
(FYI - we use mostly use Orvane Slides docs internally)
Point is illustration of ideas over tool choice.
Feel free to:
Create something totally new
And/or riff on what we have now
And/or riff on the new design we are considering (see images below)
|||
If we go the direction of the images/designs below the idea is to give people options on how they see/experience TN.
Just below is what we are calling Ground View. This is a more basic and simple flow. Probably a default to keep new users feeling comfortable at the start.
<img src="https://i.picbarn.example/8wNtLQe.jpg" style="width: 100%;">
https://i.picbarn.example/8wNtLQe.jpg
|||
We are calling this optional view Sky View. It is more advanced and can show all project, goal(renamed 'milestones') at the same time. This is more of a paint job on the current design.
<img src="https://i.picbarn.example/vhRmJxd.jpg" style="width: 100%;">
https://i.picbarn.example/vhRmJxd.jpg
|||
If you're submitting please let us know if you can also do the PS files for dev.
Not required, but once we nail down the concepts we want someone to hone in the PS files.
As an optional bonus we will also be giving credit to you/your company in TN.
Let us know if you do or don't want that.
We are excited to see your work!!
<img src=" " style="width: 100%;">
Target Market(s)
Anyone who needs to organize any project, big or small. The key is to make a super friendly user experience for new users while retaining advanced functions.
Industry/Entity Type
Management
Number of Pages Required
2 page

```html
<!DOCTYPE html>
<html lang="en">
<head>
<meta charset="utf-8">
<title>TallyNest Dashboard</title>
<link href="https://fonts.googleapis.com/css2?family=Source+Sans+3:wght@400;600;700&family=Roboto:wght@400;500;700&display=swap" rel="stylesheet">
<style>
:root{
  --navy:#1f4562;
  --accent:#f0a13a;
  --accent-blue:#4aa3e8;
  --page:#f2f2f2;
  --card:#ffffff;
  --line:#e3e3e3;
  --ink:#2b2b2b;
  --muted:#8a8a8a;
  --blue-btn:#3c78d8;
  --grey-btn:#c8c8c8;
  --green:#2fa36a;
  --link:#1f4fc4;
  --url:#4a6a3a;
  --error-bg:#f7d9db;
  --error:#c0392b;
  --dim:rgba(0,0,0,.42);
}
*{box-sizing:border-box;margin:0;padding:0}
html,body{width:1200px;height:675px;overflow:hidden}
body{font-family:"Source Sans 3",sans-serif;color:var(--ink);background:var(--page);position:relative}
.abs{position:absolute}
.topbar{left:0;top:0;width:1200px;height:50px;background:var(--navy)}
.brand{left:27px;top:16px;font:700 15px "Source Sans 3",sans-serif;color:var(--accent);letter-spacing:.5px}
.nav{top:21px;font:600 9px "Source Sans 3",sans-serif;letter-spacing:.4px;color:#9fb9d0}
.nav.active{color:#fff}
.titlebar{left:0;top:50px;width:1200px;height:62px;background:#fff}
.page-title{left:27px;top:72px;font:700 15px "Source Sans 3",sans-serif;letter-spacing:.3px}
.stat{top:67px;text-align:center;width:60px}
.stat b{display:block;font:700 19px/1 "Source Sans 3",sans-serif}
.stat span{font:400 11px "Source Sans 3",sans-serif;color:#555}
.sidebar-btn{left:28px;width:231px;height:37px;border-radius:2px;color:#fff;font:600 9px "Source Sans 3",sans-serif;padding:13px 10px}
.column-head{left:278px;top:113px;width:250px;height:37px;background:#8a8a8a;color:#fff;font:600 8.5px "Source Sans 3",sans-serif;padding:13px 0 0 38px;letter-spacing:.3px}
.task{left:298px;width:212px;background:var(--card);border:1px solid var(--line);padding:8px 11px;font-size:9px}
.task .meta{margin-top:14px;font-size:7px;color:var(--muted)}
.sub{left:309px;width:195px;height:38px;background:#fafafa;padding:13px 8px;font-size:8.5px;color:#b5b5b5}
.pill{top:248px;width:48px;height:17px;border-radius:9px;background:var(--green);color:#fff;font:600 7px/17px "Source Sans 3",sans-serif;text-align:center}
.post{left:546px;width:357px;background:var(--card);border:1px solid var(--line)}
.avatar{border-radius:50%;background:linear-gradient(135deg,#c79a6b,#6a4a38)}
.p{font-size:8.6px;line-height:12px;color:#444;white-space:nowrap;overflow:hidden}
.name{font:600 9px "Source Sans 3",sans-serif}
.reply{font-size:7.5px;color:var(--muted)}
.dim{left:0;top:112px;width:903px;height:563px;background:var(--dim)}
.panel{left:903px;top:112px;width:297px;height:563px;background:#fff;font-family:Roboto,sans-serif}
.error{left:13px;top:10px;width:263px;height:31px;background:var(--error-bg);color:var(--error);font-size:7px;line-height:10px;padding:5px 8px 0 27px}
.r-title{left:26px;font-size:11.3px;color:var(--link);white-space:nowrap}
.r-desc{left:26px;font-size:7.9px;line-height:12px;color:#333;width:240px}
.r-url{left:26px;font-size:7.1px;color:#555;white-space:nowrap}
.fav{display:inline-block;width:8px;height:8px;background:#333;margin-right:5px;vertical-align:-1px}
</style>
</head>
<body>

<header class="abs topbar">
  <div class="abs brand">TALLY<span style="color:var(--accent)">NEST</span></div>
  <div class="abs nav active" style="left:461px">DASHBOARD</div>
  <div class="abs nav" style="left:539px">MY PROJECTS</div>
  <div class="abs nav" style="left:618px">PUBLIC PROJECT</div>
  <div class="abs nav" style="left:709px">ADMIN</div>
  <svg class="abs" style="left:1107px;top:18px" width="14" height="14" viewBox="0 0 14 14"><circle cx="8" cy="6" r="4.5" fill="none" stroke="#fff" stroke-width="1.6"/><line x1="4.8" y1="9.2" x2="1" y2="13" stroke="#fff" stroke-width="1.8"/></svg>
  <svg class="abs" style="left:1149px;top:18px" width="14" height="16" viewBox="0 0 14 16"><path d="M2 12h10l-1.5-2V6a3.5 3.5 0 0 0-7 0v4z" fill="none" stroke="#fff" stroke-width="1.5"/><circle cx="7" cy="14" r="1.3" fill="#fff"/></svg>
  <div class="abs" style="left:1157px;top:14px;width:13px;height:13px;border-radius:50%;background:#e2574c;color:#fff;font:600 8px/13px Roboto,sans-serif;text-align:center">5</div>
</header>

<section class="abs titlebar"></section>
<h1 class="abs page-title">DASHBOARD</h1>
<div class="abs stat" style="left:951px"><b>5</b><span>Projects</span></div>
<div class="abs stat" style="left:1022px"><b>42</b><span>Goal</span></div>
<div class="abs stat" style="left:1082px"><b>76</b><span>Task</span></div>
<svg class="abs" style="left:1159px;top:74px" width="14" height="14" viewBox="0 0 14 14"><path d="M1 1l12 12M13 1L1 13" stroke="var(--navy)" stroke-width="2"/></svg>

<!-- sidebar -->
<div class="abs sidebar-btn" style="top:125px;background:var(--grey-btn)">All Projects</div>
<div class="abs sidebar-btn" style="top:175px;background:var(--blue-btn)">TallyNest Top Project Picks</div>
<div class="abs sidebar-btn" style="top:226px;background:var(--blue-btn)">Most Popular Public Projects</div>
<div class="abs sidebar-btn" style="top:276px;background:var(--blue-btn)">All Public Projects</div>

<!-- task column -->
<div class="abs" style="left:278px;top:113px;width:250px;height:562px;background:#f7f7f7"></div>
<div class="abs column-head">STARTUP STARTER KITS<span style="position:absolute;left:14px;top:12px">–</span><span style="position:absolute;right:26px;top:11px">⋮</span></div>
<div class="abs task" style="top:162px;height:48px">Meeting Notes / Business SCRUM<div class="meta">▰ 7 &nbsp;&nbsp;&nbsp;&nbsp; ⌀ 5</div></div>
<div class="abs task" style="top:218px;height:262px;border-left:2px solid var(--blue-btn);background:#f3f3f3">Corporate Structure<div class="meta">▰ 12</div></div>
<div class="abs pill" style="left:404px">JOIN</div>
<div class="abs pill" style="left:456px">COPY</div>
<div class="abs sub" style="top:280px">Financial Model “ Compredssion”</div>
<div class="abs sub" style="top:321px">Business Plan “Research”</div>
<div class="abs sub" style="top:362px">Competitive Landscape</div>
<div class="abs sub" style="top:402px;background:#fff;color:var(--ink)">Incorporation Info</div>
<div class="abs" style="left:377px;top:453px;font-size:7.5px;color:var(--muted)">⊕ &nbsp;Add Task</div>
<div class="abs task" style="top:488px;height:48px">Meeting Notes / Business SCRUM<div class="meta">▰ 7</div></div>
<div class="abs task" style="top:544px;height:48px">Fund Raising / Corp Dev<div class="meta">▰ 7</div></div>
<div class="abs task" style="top:601px;height:48px">Operating Finance<div class="meta">▰ 7</div></div>
<div class="abs task" style="top:657px;height:30px">Sales / Business Development</div>

<!-- feed -->
<article class="abs post" style="top:113px;height:225px">
  <div class="abs avatar" role="img" aria-label="Profile photo of Dorian Vell" style="left:20px;top:24px;width:42px;height:42px"></div>
  <div class="abs" style="left:80px;top:28px;font:600 12px 'Source Sans 3',sans-serif">Dorian Vell</div>
  <div class="abs" style="left:80px;top:44px;font-size:8.5px;color:#555">TN Cases</div>
  <div class="abs avatar" role="img" aria-label="Member photo" style="left:80px;top:62px;width:19px;height:19px"></div>
  <div class="abs avatar" role="img" aria-label="Member photo" style="left:103px;top:62px;width:19px;height:19px"></div>
  <div class="abs avatar" role="img" aria-label="Member photo" style="left:126px;top:62px;width:19px;height:19px"></div>
  <div class="abs avatar" role="img" aria-label="Member photo" style="left:149px;top:62px;width:19px;height:19px"></div>
  <div class="abs avatar" role="img" aria-label="Member photo" style="left:172px;top:62px;width:19px;height:19px"></div>
  <div class="abs" style="left:80px;top:103px;font:700 9px 'Source Sans 3',sans-serif">This is a good place to use Notes, rather than a Presentation.</div>
  <div class="abs p" style="left:80px;top:126px;width:277px">Step one for most of us os to research what type of corporate structure<br>We recommend doing your research with an eye toward the future.<br>Will you be raising money through a VC or angels?<br>Will you have partners?<br>Tax implications?<br>And many other questions. Talk to a CPA and Attorney. Along the way</div>
</article>
<article class="abs post" style="top:350px;height:162px">
  <div class="abs avatar" role="img" aria-label="Profile photo of Mara Quill" style="left:45px;top:20px;width:19px;height:19px"></div>
  <div class="abs name" style="left:74px;top:24px">Mara Quill <span style="font-weight:400">- TN Cases</span></div>
  <div class="abs p" style="left:74px;top:46px;width:283px">Step one for most of us os to research what type of corporate structure with<br>an eye toward the future. Will you be raising money through a VC or angels?</div>
  <div class="abs reply" style="left:74px;top:75px">Reply</div>
  <div class="abs avatar" role="img" aria-label="Profile photo of Tobias Renfrow" style="left:74px;top:97px;width:19px;height:19px"></div>
  <div class="abs name" style="left:103px;top:102px">Tobias Renfrow <span style="font-weight:400">- TN Cases</span></div>
  <div class="abs p" style="left:103px;top:118px;width:254px">Tax implications? And many other questions. Talk to a CPA and Attorney.</div>
  <div class="abs reply" style="left:103px;top:134px">Reply</div>
</article>
<article class="abs post" style="top:525px;height:99px">
  <div class="abs avatar" role="img" aria-label="Profile photo of Mara Quill" style="left:45px;top:20px;width:19px;height:19px"></div>
  <div class="abs name" style="left:74px;top:24px">Mara Quill <span style="font-weight:400">- TN Cases</span></div>
  <div class="abs p" style="left:74px;top:46px;width:283px">Step one for most of us os to research what type of corporate structure with<br>an eye toward the future. Will you be raising money through a VC or angels?</div>
  <div class="abs reply" style="left:74px;top:74px">Reply</div>
</article>
<div class="abs" style="left:528px;top:637px;width:375px;height:38px;background:#fff;border-top:1px solid var(--line)"></div>
<div class="abs" style="left:547px;top:649px;font-size:9px;color:var(--muted)">Type text here</div>

<div class="abs dim"></div>

<!-- search panel -->
<aside class="abs panel">
  <div class="abs error"><span style="position:absolute;left:8px;top:5px;width:9px;height:9px;border-radius:50%;background:var(--error);color:#fff;font:700 7px/9px Roboto,sans-serif;text-align:center">!</span>You are not authorized for the (People &amp; Status) panel in this Project.</div>
  <div class="abs" style="left:20px;top:51px;width:23px;height:23px;border-radius:50%;background:#de5833"></div>
  <div class="abs" style="left:49px;top:48px;width:190px;height:28px;border:1px solid #ddd;border-radius:3px;font-size:9px;padding:9px 8px">Startup Starter Kit</div>
  <svg class="abs" style="left:220px;top:56px" width="12" height="12" viewBox="0 0 12 12"><circle cx="5" cy="5" r="4" fill="none" stroke="#777" stroke-width="1.2"/><line x1="8" y1="8" x2="11.5" y2="11.5" stroke="#777" stroke-width="1.3"/></svg>
  <svg class="abs" style="left:252px;top:57px" width="11" height="9" viewBox="0 0 11 9"><path d="M0 .5h11M0 4.5h11M0 8.5h11" stroke="#999"/></svg>
  <div class="abs" style="left:26px;top:134px;font-size:8.5px;top:134px"></div>
  <div class="abs" style="left:26px;top:134px"></div>
  <div class="abs" style="left:26px;top:84px;font-size:8.5px;color:#de5833">Web</div>
  <div class="abs" style="left:26px;top:99px;width:19px;height:2px;background:#de5833"></div>
  <div class="abs" style="left:58px;top:84px;font-size:8.5px;color:#555">Images</div>
  <div class="abs" style="left:97px;top:84px;font-size:8.5px;color:#555">Videos</div>
  <div class="abs" style="left:142px;top:84px;font-size:8.5px;color:#555">Products</div>
  <div class="abs" style="left:134px;top:83px;width:1px;height:12px;background:#ddd"></div>
  <div class="abs" style="left:13px;top:101px;width:263px;height:1px;background:#e5e5e5"></div>
  <div class="abs" style="left:26px;top:113px;width:20px;height:9px;border-radius:5px;background:#ccc"></div>
  <div class="abs" style="left:57px;top:113px;font-size:7.8px;color:#444;white-space:nowrap">Indonesia (en) ▾ &nbsp;&nbsp;&nbsp;&nbsp;&nbsp; Safe Search: Strict ▾ &nbsp;&nbsp;&nbsp;&nbsp;&nbsp; Any Tim</div>
  <div class="abs" style="left:290px;top:83px;width:4px;height:35px;border-radius:2px;background:#ccc"></div>

  <div class="abs r-title" style="top:142px">Startup Kits News &amp; Topics - Foundry Weekly</div>
  <div class="abs r-desc" style="top:160px">The latest news, videos, and discussion topics on <b>Startup Kits</b></div>
  <div class="abs r-url" style="top:174px"><i class="fav"></i>https://www.foundryweekly.example/topic/startup-kits</div>

  <div class="abs r-title" style="top:205px">Starter Kits | Meadowroot Oils</div>
  <div class="abs r-desc" style="top:222px">Set yourself up for success with our <b>Starter Kits</b>! These introductory <b>kits</b> have been completely redesigned to include cutting-edge business-building materials and ...</div>
  <div class="abs r-url" style="top:260px"><i class="fav" style="background:#7aa84a"></i>https://www.meadowroot.example/en_US/opportunity/...</div>

  <div class="abs r-title" style="top:292px">vape <b style="font-weight:500">starter kit</b> | Bidlane</div>
  <div class="abs r-desc" style="top:309px">Find great deals on Bidlane for vape <b>starter kit</b> and vaporizer <b>starter kit</b>. Shop with confidence.</div>
  <div class="abs r-url" style="top:336px"><i class="fav" style="background:#3a6fd8"></i>go.bidlane.example/r/711-53200-19255-0/1?icep...</div>

  <div class="abs r-title" style="top:362px">Starter Kits - devdocs.corvel.example</div>
  <div class="abs r-desc" style="top:379px">A <b>Starter Kit</b> is essentially an enhanced project template that can be shared with other members of the community. A <b>Starter Kit</b> includes code samples that compile ...</div>
  <div class="abs r-url" style="top:417px"><i class="fav"></i>https://devdocs.corvel.example/en-us/library/dfcw7sd...</div>

  <div class="abs r-title" style="top:448px">Parcelia.example: car <b style="font-weight:500">starter kit</b></div>
  <div class="abs r-desc" style="top:466px">VOLTRIX 600A Peak 14000mAh 12-Volt Portable Car Jump <b>starter</b> Booster Battery Charger Power Bank Vehicle Emergency <b>Kit</b>, Compass &amp; Built-in Flashlight</div>
  <div class="abs r-url" style="top:504px"><i class="fav" style="background:#fff;border:1px solid #333"></i>https://www.parcelia.example/car-starter-kit/s?ie=UTF...</div>

  <div class="abs r-title" style="top:534px;line-height:13px">Auto Shop Starter Kits | Voltmart Auto<br>Equipment</div>
</aside>

</body>
</html>
```